KORVA needs a beautiful/corp web page

We are a pump an compressor repair facility in Alberta Canada. We love clean looks. white yellows greens blues. main page should involve conola fields, sun shine

Reason: i will be guaranteeing the project keep up the good work

Requirements
Must have
• open conola fields

```html
<!DOCTYPE html>
<html lang="en">
<head>
<meta charset="utf-8">
<title>KORVA — Pump &amp; Compressor Repair</title>
<link href="https://fonts.googleapis.com/css2?family=Questrial&family=Open+Sans:wght@400;600&display=swap" rel="stylesheet">
<style>
:root{
  --yellow:#ffb400;
  --yellow-soft:#ffc233;
  --green:#c2dd62;
  --green-band:#a9d42a;
  --blue:#74bfd3;
  --blue-band:#1992bb;
  --ink:#2e2e2e;
  --grey:#6b6b6b;
  --line:#dcdcdc;
  --footer:#2b2728;
  --footer-text:#8a8585;
  --placeholder-a:#e4d664;
  --placeholder-b:#d9c94a;
}
*{margin:0;padding:0;box-sizing:border-box}
html,body{width:887px;height:1200px;overflow:hidden;background:#fff}
body{font-family:"Open Sans",sans-serif;color:var(--ink)}
.page{position:relative;width:887px;height:1200px;overflow:hidden}
.abs{position:absolute}

.hero-photo{left:0;top:0;width:887px;height:404px;background:linear-gradient(180deg,var(--placeholder-a),var(--placeholder-b))}
.header{left:0;top:0;width:887px;height:67px;background:rgba(246,249,252,.94);border-top:3px solid var(--yellow)}
.header-accent{left:56px;top:0;width:194px;height:3px;background:#333}
.brand{left:80px;top:20px;display:flex;align-items:center;gap:8px;font-family:"Questrial",sans-serif;font-size:26px;color:var(--ink);letter-spacing:1px}
.brand-mark{width:14px;height:14px;background:var(--yellow)}
.nav{top:0;height:67px;font-family:"Questrial",sans-serif;font-size:9.5px;letter-spacing:.8px;color:var(--ink);line-height:67px}
.nav-home{left:457px;width:48px;background:var(--yellow-soft);text-align:center;color:#5a3c00}
.nav-divider{left:790px;top:27px;width:1px;height:20px;background:#ccc}
.search{left:804px;top:27px;width:20px;height:20px;background:var(--yellow)}

.headline{left:69px;padding:0 12px;background:rgba(255,255,255,.6);font-family:"Questrial",sans-serif;font-size:31px;letter-spacing:3.2px;color:#2b2b2b;white-space:nowrap}
.headline-1{top:200px;height:47px;line-height:47px;width:549px}
.headline-2{top:249px;height:46px;line-height:46px;width:572px}

.band-label{left:0;top:404px;width:250px;height:32px;background:var(--blue-band);color:#fff;font-size:13.5px;letter-spacing:.5px;line-height:32px;text-align:center}
.band-text{left:250px;top:404px;width:637px;height:32px;background:var(--green-band);color:#fff;font-size:11px;line-height:32px;padding-left:29px;letter-spacing:.3px}

.card{top:495px;width:186px;height:185px;text-align:center;color:#fff}
.card svg{position:absolute;left:70px;top:28px}
.card-title{position:absolute;top:99px;width:100%;font-family:"Questrial",sans-serif;font-size:12.5px;letter-spacing:1.4px}
.card-body{position:absolute;top:135px;left:10px;right:10px;font-size:8.2px;line-height:10px;font-weight:600}
.card-1{left:60px;background:var(--yellow)}
.card-2{left:253px;background:var(--yellow-soft)}
.card-3{left:446px;background:var(--green)}
.card-4{left:638px;background:var(--blue)}

.section-rule{height:1px;background:var(--line)}
.section-dot{width:7px;height:7px;border-radius:50%;background:var(--line)}
.section-title{font-family:"Questrial",sans-serif;font-size:17px;letter-spacing:2.4px;color:#222;width:160px;text-align:center}

.news-photo{width:111px;height:81px;background:linear-gradient(180deg,var(--placeholder-a),var(--placeholder-b))}
.news-count{width:64px;height:12px;color:#fff;font-size:6px;line-height:12px;padding-left:6px;letter-spacing:.3px}
.news-icon{width:26px;height:26px}
.news-title{font-family:"Questrial",sans-serif;font-size:11px;letter-spacing:.6px;color:#222}
.news-date{font-size:7px;letter-spacing:.4px;color:#777}
.news-body{font-size:8.3px;line-height:9.8px;color:#555;width:240px}
.read-more{width:80px;height:16px;color:#fff;font-size:8.5px;font-weight:600;text-align:center;line-height:16px}

.clients{left:70px;top:999px;width:748px;height:75px;border:1px solid #ddd;display:flex;justify-content:space-around;align-items:center;font-family:"Questrial",sans-serif;font-size:15px;color:#8a8a8a;letter-spacing:1px}
.client{display:flex;align-items:center;gap:6px}
.client-first{color:#c9202a}
.client-dot{width:9px;height:9px;border-radius:50%;background:#bdbdbd}

.footer{left:0;top:1120px;width:887px;height:80px;background:var(--footer);text-align:center;font-family:"Questrial",sans-serif;color:var(--footer-text);letter-spacing:1px}
.footer-nav{margin-top:16px;font-size:10px}
.footer-info{margin-top:6px;font-size:9px}
.footer span.sep{margin:0 9px}
</style>
</head>
<body>
<div class="page">

  <div class="abs hero-photo" role="img" aria-label="Photo placeholder: open canola field in sunshine under a blue sky"></div>

  <header class="abs header"></header>
  <div class="abs header-accent"></div>
  <div class="abs brand"><span>KORVA</span><span class="brand-mark"></span></div>
  <div class="abs nav nav-home">HOME</div>
  <div class="abs nav" style="left:522px">SOLUTIONS</div>
  <div class="abs nav" style="left:597px">PRODUCTS</div>
  <div class="abs nav" style="left:674px">ABOUT</div>
  <div class="abs nav" style="left:732px">CONTACT</div>
  <div class="abs nav-divider"></div>
  <div class="abs search">
    <svg width="20" height="20" viewBox="0 0 20 20"><circle cx="9" cy="9" r="4" fill="none" stroke="#fff" stroke-width="1.6"/><line x1="12" y1="12" x2="15" y2="15" stroke="#fff" stroke-width="1.8"/></svg>
  </div>

  <div class="abs headline headline-1">We are a pump an compressor</div>
  <div class="abs headline headline-2">repair facility in Alberta Canada</div>

  <div class="abs band-label">LOREM IPSUM DOLOR</div>
  <div class="abs band-text">Lorem ipsum dolor sit amet, consectetur adipisicing elit, sed do eiusmod tempor.</div>

  <div class="abs card card-1">
    <svg width="46" height="46" viewBox="0 0 46 46" fill="none" stroke="#fff" stroke-width="5" stroke-linejoin="round">
      <path d="M15 16 L23 5 L31 16"/><path d="M36 22 L40 34 L27 37"/><path d="M19 37 L6 34 L10 22"/>
    </svg>
    <div class="card-title">LOREM IPSUM</div>
    <div class="card-body">Sed ut perspiciatis unde omnis iste natus error sit voluptatem accusantium dolor-emque laudantium</div>
  </div>
  <div class="abs card card-2">
    <svg width="46" height="46" viewBox="0 0 46 46" fill="none" stroke="#fff" stroke-width="2.4">
      <circle cx="23" cy="23" r="20"/><ellipse cx="23" cy="23" rx="9" ry="20"/><line x1="3" y1="23" x2="43" y2="23"/><line x1="23" y1="3" x2="23" y2="43"/><path d="M7 13 H39 M7 33 H39"/>
    </svg>
    <div class="card-title">LOREM IPSUM</div>
    <div class="card-body">Sed ut perspiciatis unde omnis iste natus error sit voluptatem accusantium dolor-emque laudantium</div>
  </div>
  <div class="abs card card-3">
    <svg width="46" height="46" viewBox="0 0 46 46" fill="none" stroke="#fff" stroke-width="1.5">
      <circle cx="23" cy="23" r="12"/><circle cx="23" cy="23" r="6" fill="#fff"/><line x1="23" y1="2" x2="23" y2="44"/><line x1="2" y1="23" x2="44" y2="23"/>
    </svg>
    <div class="card-title">LOREM IPSUM</div>
    <div class="card-body">Sed ut perspiciatis unde omnis iste natus error sit voluptatem accusantium dolor-emque laudantium</div>
  </div>
  <div class="abs card card-4">
    <svg width="46" height="46" viewBox="0 0 46 46"><path d="M3 24 L10 19 L18 30 L40 4 L42 8 L18 42 Z" fill="#fff"/></svg>
    <div class="card-title">LOREM IPSUM</div>
    <div class="card-body">Sed ut perspiciatis unde omnis iste natus error sit voluptatem accusantium dolor-emque laudantium</div>
  </div>

  <div class="abs section-rule" style="left:69px;top:743px;width:295px"></div>
  <div class="abs section-dot" style="left:364px;top:740px"></div>
  <div class="abs section-title" style="left:366px;top:731px">Latest News</div>
  <div class="abs section-dot" style="left:517px;top:740px"></div>
  <div class="abs section-rule" style="left:524px;top:743px;width:293px"></div>

  <div class="abs news-photo" style="left:64px;top:781px" role="img" aria-label="Photo placeholder: canola field"></div>
  <div class="abs news-count" style="left:64px;top:850px;background:var(--blue-band)">0 COMMENTS</div>
  <div class="abs news-icon" style="left:195px;top:780px;background:var(--green-band)">
    <svg width="26" height="26" viewBox="0 0 26 26"><path d="M10 7 L16 7 L14 12 L14 19 L12 19 L12 12 Z" fill="#fff"/></svg>
  </div>
  <div class="abs news-title" style="left:231px;top:777px">Lorem ipsum dolor sit amet</div>
  <div class="abs news-date" style="left:232px;top:796px">12 OCTOBER 2013</div>
  <div class="abs news-body" style="left:194px;top:821px">&nbsp;&nbsp;&nbsp;Sed ut perspiciatis unde omnis iste natus error sit voluptatem accusantium doloremque laudantium, totam rem aperiam, eaque ipsa quae ab illo inventore veritatis et quasi arch</div>
  <div class="abs read-more" style="left:353px;top:879px;background:var(--yellow-soft)">Read more</div>

  <div class="abs news-photo" style="left:451px;top:781px" role="img" aria-label="Photo placeholder: canola field"></div>
  <div class="abs news-count" style="left:451px;top:850px;background:#777">0 COMMENTS</div>
  <div class="abs news-icon" style="left:582px;top:780px;background:#6f6f6f">
    <svg width="26" height="26" viewBox="0 0 26 26"><path d="M10 7 L16 7 L14 12 L14 19 L12 19 L12 12 Z" fill="#fff"/></svg>
  </div>
  <div class="abs news-title" style="left:618px;top:777px">Lorem ipsum dolor sit amet</div>
  <div class="abs news-date" style="left:619px;top:796px">12 OCTOBER 2013</div>
  <div class="abs news-body" style="left:581px;top:821px">&nbsp;&nbsp;&nbsp;Sed ut perspiciatis unde omnis iste natus error sit voluptatem accusantium doloremque laudantium, totam rem aperiam, eaque ipsa quae ab illo inventore veritatis et quasi arch</div>
  <div class="abs read-more" style="left:735px;top:879px;background:#777">Read more</div>

  <div class="abs section-rule" style="left:69px;top:961px;width:295px"></div>
  <div class="abs section-dot" style="left:364px;top:958px"></div>
  <div class="abs section-title" style="left:362px;top:949px">Our Clients</div>
  <div class="abs section-dot" style="left:517px;top:958px"></div>
  <div class="abs section-rule" style="left:524px;top:961px;width:293px"></div>

  <div class="abs clients">
    <div class="client client-first">Halvern</div>
    <div class="client">Ostrava</div>
    <div class="client"><span class="client-dot"></span>Brindel</div>
    <div class="client">Ketterly</div>
    <div class="client">Ezmont</div>
  </div>

  <footer class="abs footer">
    <div class="footer-nav">Home<span class="sep">I</span>Products<span class="sep">I</span>Solutions<span class="sep">I</span>Choose us<span class="sep">I</span>About us<span class="sep">I</span>Contact</div>
    <div class="footer-info">Your info mail<span class="sep">I</span>Address<span class="sep">I</span>Phone number</div>
  </footer>

</div>
</body>
</html>
```